Kestrel Home Business Card Design

We need a business card for a Building company based in Queensland, Australia. Our colours are orange black and we do base all our homes design names and other aspect of our business on astrology. We want the consumer to perceive the company as professional and to attract investors to our company.We have over 20 years in the building industry.We pride ourselves on our innovation of designs and making the building process for anyone from families to investor a smooth and simple experience.
Business
Amelia Prichard0411752116PO Box 454, Mudgeerbaameliaprichard@zodiachomes.com

```html
<!DOCTYPE html>
<html lang="en">
<head>
<meta charset="utf-8">
<title>Kestrel Homes Business Card</title>
<link rel="stylesheet" href="https://fonts.googleapis.com/css2?family=Arimo:wght@700&family=Open+Sans:wght@400;600;700&display=swap">
<style>
  :root {
    --orange: #f6921e;
    --black: #050505;
    --white: #ffffff;
    --backdrop: #d9d9d9;
  }
  * { margin: 0; padding: 0; box-sizing: border-box; }
  html, body { width: 1200px; height: 900px; overflow: hidden; }
  body {
    background: var(--backdrop);
    position: relative;
    font-family: "Open Sans", sans-serif;
    color: var(--white);
  }
  .card {
    position: absolute;
    width: 560px;
    height: 320px;
    overflow: hidden;
    background: var(--black);
  }

  /* Back of card */
  .card-back { left: 560px; top: 110px; }
  .card-back .band-top {
    position: absolute; left: 0; top: 0; width: 100%; height: 70px;
    background: var(--orange);
  }
  .card-back .band-bottom {
    position: absolute; left: 0; bottom: 0; width: 100%; height: 38px;
    background: var(--orange);
  }
  .card-back .brand {
    position: absolute; left: 0; top: 70px; width: 100%; height: 212px;
    display: flex; flex-direction: column; align-items: center; justify-content: center;
    gap: 14px;
  }
  .card-back .brand-dot {
    width: 58px; height: 58px; border-radius: 50%;
    background: var(--orange);
  }
  .brand-name {
    font-family: "Arimo", sans-serif;
    font-weight: 700;
    color: var(--white);
    letter-spacing: 0.5px;
  }
  .card-back .brand-name { font-size: 33px; }

  /* Front of card */
  .card-front { left: 110px; top: 440px; }
  .card-front .brand-dot {
    position: absolute; left: 78px; top: 22px;
    width: 158px; height: 158px; border-radius: 50%;
    background: var(--orange);
  }
  .card-front .brand-name {
    position: absolute; left: 270px; top: 98px;
    font-size: 40px;
  }
  .card-front .band-main {
    position: absolute; left: 0; top: 148px; width: 100%; height: 136px;
    background: var(--orange);
  }
  .person {
    position: absolute; left: 88px; top: 152px;
  }
  .person-name { font-size: 19px; font-weight: 700; line-height: 1.15; }
  .person-role { font-size: 12px; font-weight: 400; }
  .contact-list {
    position: absolute; right: 22px; top: 196px;
    list-style: none; text-align: right;
    font-size: 13.5px; line-height: 17px;
  }
  .contact-list li { display: flex; justify-content: flex-end; align-items: center; gap: 7px; }
  .contact-list svg { width: 11px; height: 11px; fill: var(--white); flex: none; }
  .address {
    position: absolute; left: 60px; bottom: 40px;
    font-size: 13.5px;
  }
</style>
</head>
<body>

  <section class="card card-back" aria-label="Business card back">
    <div class="band-top"></div>
    <div class="brand">
      <div class="brand-dot"></div>
      <span class="brand-name">Kestrel Homes</span>
    </div>
    <div class="band-bottom"></div>
  </section>

  <section class="card card-front" aria-label="Business card front">
    <div class="brand-dot"></div>
    <span class="brand-name">Kestrel Homes</span>
    <div class="band-main"></div>
    <div class="person">
      <p class="person-name">Harriet Colvane</p>
      <p class="person-role">Managing Director</p>
    </div>
    <ul class="contact-list">
      <li>0487 309 625
        <svg viewBox="0 0 12 12" aria-hidden="true"><path d="M1 3c0-1 1-2 2-2h6c1 0 2 1 2 2v1H8V3H4v1H1zM2 5h8l1 5H1zm4 1.3a1.6 1.6 0 1 0 0 3.2 1.6 1.6 0 0 0 0-3.2z"/></svg>
      </li>
      <li>0487 309 625
        <svg viewBox="0 0 12 12" aria-hidden="true"><path d="M3 0h6v12H3zM4 1.5v7.5h4V1.5zM6 10a.6.6 0 1 0 0 1.2A.6.6 0 0 0 6 10z"/></svg>
      </li>
      <li>harrietcolvane@kestrelhomes.example
        <svg viewBox="0 0 12 12" aria-hidden="true"><path d="M0 2h12v8H0zm1 1v.4l5 3.3 5-3.3V3z"/></svg>
      </li>
      <li>www.kestrelhomes.example
        <svg viewBox="0 0 12 12" aria-hidden="true"><path d="M5 7 7 5l.8.8-2 2zM2.5 6.5l2-2 1 1-2 2 1 1 2-2 1 1-2 2a1.4 1.4 0 0 1-2 0l-1-1a1.4 1.4 0 0 1 0-2zm4-4a1.4 1.4 0 0 1 2 0l1 1a1.4 1.4 0 0 1 0 2l-2 2-1-1 2-2-1-1-2 2-1-1z"/></svg>
      </li>
      <li>
        <svg viewBox="0 0 12 12" aria-hidden="true" style="visibility:hidden"><path d="M0 0"/></svg>
      </li>
    </ul>
    <p class="address">PO Box 872, Ridgewell QLD 4213 &nbsp;
      <svg viewBox="0 0 12 12" width="11" height="11" aria-hidden="true" style="fill:var(--white);vertical-align:-1px"><path d="M6 0a4 4 0 0 0-4 4c0 3 4 8 4 8s4-5 4-8a4 4 0 0 0-4-4zm0 2.4a1.6 1.6 0 1 1 0 3.2 1.6 1.6 0 0 1 0-3.2z"/></svg>
    </p>
  </section>

</body>
</html>
```